Business Card Design for Occupational Medicine Start Up Company

We need to design a professional business card. We are a healthcare company providing occupational medicine services to blue collar industries. We are professional, efficient and high quality service providers.

Target Market(s)

Blue Collar Industry: Shipbuilding, Ports, Trucking Companies; The Executives and Safety Officers for these companies

Industry/Entity Type

Healthcare

Contact Information for Business Card

Logo, Name, Title, Email, Phone

Other font styles liked:
• Please match our Brand Guide

Requirements
Must have
• Our Company Colors and Logo

```html
<!DOCTYPE html>
<html lang="en">
<head>
<meta charset="UTF-8">
<title>Crewline Care — Business Card</title>
<link href="https://fonts.googleapis.com/css2?family=Montserrat:wght@700;800&family=Open+Sans:wght@400;600&display=swap" rel="stylesheet">
<style>
  :root {
    --navy: #27317f;
    --navy-deep: #232b78;
    --pattern: #2d3a92;
    --orange: #f0a53a;
    --grey-text: #5f5f66;
    --rule: #9a9aa0;
    --white: #ffffff;
    --stage: #2b2b2d;
  }
  * { box-sizing: border-box; margin: 0; padding: 0; }
  html, body {
    width: 1200px; height: 1108px; overflow: hidden;
    background: var(--stage);
  }
  .stage {
    position: relative; width: 1200px; height: 1108px;
    display: flex; justify-content: center; align-items: center; gap: 70px;
  }
  .card {
    width: 370px; height: 630px; border-radius: 26px;
    position: relative; overflow: hidden;
  }
  /* Back side */
  .card-back { background: var(--navy-deep); }
  .card-back .pattern-field {
    position: absolute; inset: 0;
    background: linear-gradient(160deg, var(--pattern) 0%, var(--navy-deep) 70%);
  }
  .card-back .back-mark {
    position: absolute; right: 48px; bottom: 150px;
    display: flex; align-items: center; gap: 8px;
    font-family: "Montserrat", sans-serif; font-weight: 800;
    font-size: 17px; color: var(--white); letter-spacing: 0.5px;
  }
  .mark-dot {
    width: 14px; height: 14px; border-radius: 50%; background: var(--orange);
  }
  /* Front side */
  .card-front {
    background: var(--white);
    display: flex; flex-direction: column; align-items: center;
    padding-top: 150px; text-align: center;
  }
  .brand {
    display: flex; align-items: center; gap: 10px;
    font-family: "Montserrat", sans-serif; font-weight: 800;
    font-size: 30px; color: var(--navy); letter-spacing: 0.5px;
  }
  .brand .mark-dot { width: 20px; height: 20px; }
  .person-name {
    margin-top: 48px;
    font-family: "Montserrat", sans-serif; font-weight: 800;
    font-size: 32px; color: var(--navy); letter-spacing: 0.5px;
  }
  .person-title {
    margin-top: 2px;
    font-family: "Open Sans", sans-serif; font-size: 17px; color: var(--grey-text);
  }
  .icon-row {
    margin-top: 10px; width: 290px;
    display: flex; align-items: center; gap: 8px;
  }
  .icon-row .rule { flex: 1; height: 1px; background: var(--rule); }
  .icon-box {
    width: 32px; height: 32px; border-radius: 5px; background: var(--orange);
    display: flex; align-items: center; justify-content: center;
  }
  .contact {
    margin-top: 14px;
    font-family: "Open Sans", sans-serif; font-size: 18px; line-height: 1.5;
    color: var(--grey-text);
  }
  .contact .accent { color: var(--orange); }
  .divider { width: 290px; height: 1px; background: var(--rule); margin: 10px 0; }
  .address {
    font-family: "Open Sans", sans-serif; font-size: 17px; line-height: 1.35;
    color: var(--grey-text);
  }
</style>
</head>
<body>
<main class="stage">
  <section class="card card-back" aria-label="Card back">
    <div class="pattern-field" role="img" aria-label="Tonal repeating brand pattern on navy"></div>
    <div class="back-mark"><span class="mark-dot"></span>Crewline Care</div>
  </section>

  <section class="card card-front" aria-label="Card front">
    <div class="brand"><span class="mark-dot"></span>Crewline Care</div>
    <h1 class="person-name">DANA BROOKS</h1>
    <p class="person-title">Manager</p>
    <div class="icon-row">
      <span class="rule"></span>
      <span class="icon-box">
        <svg width="18" height="18" viewBox="0 0 24 24" fill="none" stroke="#fff" stroke-width="2" aria-hidden="true"><path d="M5 3h4l2 5-3 2a11 11 0 0 0 6 6l2-3 5 2v4a2 2 0 0 1-2 2A17 17 0 0 1 3 5a2 2 0 0 1 2-2z"/></svg>
      </span>
      <span class="icon-box">
        <svg width="20" height="16" viewBox="0 0 24 18" fill="none" stroke="#fff" stroke-width="2" aria-hidden="true"><rect x="2" y="2" width="20" height="14" rx="1"/><path d="M2 3l10 7 10-7"/></svg>
      </span>
      <span class="icon-box">
        <svg width="18" height="18" viewBox="0 0 24 24" fill="none" stroke="#fff" stroke-width="1.8" aria-hidden="true"><circle cx="12" cy="12" r="9"/><ellipse cx="12" cy="12" rx="4" ry="9"/><path d="M3 12h18M5 7h14M5 17h14"/></svg>
      </span>
      <span class="rule"></span>
    </div>
    <p class="contact">555-014-2290<br>info@crewlinecare.com<br>www.<span class="accent">crewlinecare</span>.com</p>
    <div class="divider"></div>
    <p class="address">480 Harbor View Rd. Suite 210<br>Dallas, TX 75201</p>
  </section>
</main>
</body>
</html>
```